Customer Value Leaflet

We need a bi-fold brochure designing, based on the attached PDF wireframes. Our company name is brambleharvik.com (of which the logo is currently being designed). The corporate colour is orange (the exact shade of which we are happy to leave to the designers discretion).

The leaflet will distributed to customer experience experts and marketers so the design needs to be bright, engaging, clean and simple. Design is critical.

It Company

```html
<!DOCTYPE html>
<html lang="en">
<head>
<meta charset="utf-8">
<title>Customer Value Leaflet – Kim and Kevin</title>
<link href="https://fonts.googleapis.com/css2?family=Open+Sans:wght@300;400&display=swap" rel="stylesheet">
<style>
  :root {
    --paper: #ffffff;
    --paper-tint: #f8f8f8;
    --timeline-green: #1f9a3c;
    --brand-orange: #f7a823;
    --text-grey: #6a6a6a;
    --text-dark: #333333;
    --icon-orange: #f0a020;
    --icon-orange-deep: #d98a10;
    --icon-muted: #c9b59a;
    --stop-red: #d7262b;
  }
  * { margin: 0; padding: 0; box-sizing: border-box; }
  html, body { width: 1200px; height: 1200px; overflow: hidden; }
  body {
    background: var(--paper);
    font-family: "Open Sans", Arial, sans-serif;
    font-weight: 300;
    color: var(--text-grey);
  }
  .leaflet {
    position: relative;
    width: 1200px;
    height: 1200px;
    background: var(--paper-tint);
  }
  .timeline {
    position: absolute;
    left: 0; top: 0;
    width: 1200px; height: 1000px;
  }
  .timeline-label {
    fill: var(--paper);
    font-family: "Open Sans", Arial, sans-serif;
    font-size: 27px;
    font-weight: 400;
    letter-spacing: 1px;
  }
  .story-step {
    position: absolute;
    width: 460px;
    text-align: center;
  }
  .story-step--kim { left: 45px; }
  .story-step--kevin { left: 695px; }
  .step-icon {
    margin: 0 auto;
    border-radius: 18px;
  }
  .step-text {
    font-size: 27px;
    line-height: 36px;
  }
  .icon-agent { width: 150px; height: 125px;
    background: linear-gradient(180deg, var(--icon-muted), #a89478); }
  .icon-basket { width: 150px; height: 110px;
    background: linear-gradient(180deg, var(--icon-orange), var(--icon-orange-deep)); }
  .icon-cart { width: 165px; height: 125px;
    background: linear-gradient(180deg, var(--icon-orange), var(--icon-orange-deep)); }
  .icon-stop { width: 118px; height: 118px;
    background: var(--stop-red); }
  .social-name {
    height: 150px;
    display: flex; align-items: center; justify-content: center;
    font-size: 44px;
    font-weight: 400;
    color: var(--timeline-green);
  }
  .reveal-band {
    position: absolute;
    left: 0; top: 1008px;
    width: 1200px; height: 167px;
    background: var(--brand-orange);
    display: flex; align-items: center; justify-content: center;
    font-size: 34px;
    font-weight: 400;
    color: var(--text-dark);
  }
  .footer-strip {
    position: absolute;
    left: 0; top: 1175px;
    width: 1200px; height: 25px;
    background: var(--paper);
  }
</style>
</head>
<body>
<main class="leaflet">

  <svg class="timeline" viewBox="0 0 1200 1000" aria-hidden="true">
    <rect x="567" y="25" width="91" height="272" fill="var(--timeline-green)"/>
    <rect x="567" y="308" width="91" height="330" fill="var(--timeline-green)"/>
    <polygon points="567,650 658,650 658,867 717,867 612,975 508,867 567,867" fill="var(--timeline-green)"/>
    <text class="timeline-label" transform="translate(622 225) rotate(-90)">+ 1 WEEK</text>
    <text class="timeline-label" transform="translate(622 575) rotate(-90)">+ 1 MONTH</text>
    <text class="timeline-label" transform="translate(622 905) rotate(-90)">+ 6 MONTHS</text>
  </svg>

  <section class="story-step story-step--kim" style="top:83px">
    <div class="step-icon icon-agent" role="img" aria-label="Illustration of a customer service agent"></div>
    <p class="step-text" style="margin-top:20px">Kim calls you to return<br>an item...</p>
  </section>

  <section class="story-step story-step--kim" style="top:370px">
    <div class="step-icon icon-cart" role="img" aria-label="Illustration of an orange shopping cart"></div>
    <p class="step-text" style="margin-top:14px">places 4 more online<br>orders...</p>
  </section>

  <section class="story-step story-step--kim" style="top:667px">
    <div class="step-icon icon-stop" role="img" aria-label="Illustration of a red stop sign"></div>
    <p class="step-text" style="margin-top:52px">then places another<br>order but doesn’t come<br>back for a month</p>
  </section>

  <section class="story-step story-step--kevin" style="top:75px">
    <div class="step-icon icon-basket" role="img" aria-label="Illustration of an orange shopping basket"></div>
    <p class="step-text" style="margin-top:40px">Kevin makes another<br>purchase...</p>
  </section>

  <section class="story-step story-step--kevin" style="top:350px">
    <div class="social-name">Chirpline</div>
    <p class="step-text" style="margin-top:9px">then 2 more (and even<br>tweets about how<br>great your service is)...</p>
  </section>

  <section class="story-step story-step--kevin" style="top:667px">
    <div class="step-icon icon-cart" role="img" aria-label="Illustration of an orange shopping cart"></div>
    <p class="step-text" style="margin-top:45px">and continues to make<br>purchases on a<br>bi-monthly basis</p>
  </section>

  <div class="reveal-band">but really it is Kevin.</div>
  <div class="footer-strip"></div>

</main>
</body>
</html>
```